Design eines Hausetiketts für traditionelles Weingut
Zielgruppe
Wir das Familienweingut Brandauer in Gimbsheim/Rheinhessen sind ein traditionelles Weingut das seine Reben selbst kultiviert und die Weine auch selbst ausbaut. Wir haben jeden Schritt in der Weinherstellung selbst in der Hand und vermarkten den Wein dann an unsere Privatkunden. Unsere Kundenstruktur sieht folgendermaßen aus: Wir haben 100% Privatkunden die unseren Wein konsumieren. Da jetzt die nächste Generation in den Weinbaubetrieb einsteigt und auch Ideen hat möchten wir ein Hausetikett einführen. Im Moment haben wir noch sehr viele unterschiedliche Etiketten und kein Hausetikett. Da die Verlagsetiketten immer seltener zu unseren Vorstellungen passen, möchten wir hier auf diesem Wege ein Hausetikett anfertigen lassen. Generell möchten wir unseren Außenauftritt komplett modernisieren. Sie können sich über die Vielfalt in unserem Betrieb unter www.weingut-brandauer-beispiel.de einen Überblick verschaffen. Langfristig gesehen wollen wir aber unsere Weinkarte verkleinern.
Aufgabenstellung
Wir haben uns vor ca. 1,5 Jahren hier auf dieser Website bereits ein Logo designen lassen. Es wäre schön wenn man das Logo bei den Entwürfen für die Etiketten berücksichtigen würde. Das wäre aber KEIN MUSS. Auch wäre es gut wenn man das ,,Wein' bei unserem Namen weglassen könnte.
Das Etikett sollte aus Vorder-und Rückenetikett bestehen und edel wirken. Vorne sollte die Rebsorte und die Geschmacksangabe stehen. Der Rest sollte auf das Rückenetikett.
Das Vorderetikett sollte ein richtiger Eyecatcher sein und im Supermarkt z.B. aus vielen anderen herausstechen. Das wäre ganz wichtig.
Man kann bei den Farben unterscheiden in 3 Konzepte.
Literwein als einsteiger Wein
Dann die Gutsweine und zum Schluss die Lagenweine. Alles Farblich oder im design etwas abgesetzt.

```html
<!DOCTYPE html>
<html lang="de">
<head>
<meta charset="utf-8">
<title>Brandauer – Hausetikett</title>
<link rel="stylesheet" href="https://fonts.googleapis.com/css2?family=Marcellus&family=Jost:wght@300;700&family=Josefin+Sans:wght@300&family=Oswald:wght@600&display=swap">
<style>
  :root {
    --paper: #ffffff;
    --ink: #111111;
    --gold: #a88c5a;
    --sky: #97e1ea;
    --sky-light: #bbe3ea;
    --sky-deep: #91c9d2;
    --peach: #ecb898;
    --peach-light: #f0cbb3;
    --river: #9cbcc0;
    --earth: #b68f6e;
    --sand: #c9b7a2;
    --initial: #141414;
  }
  * { margin: 0; padding: 0; box-sizing: border-box; }
  html, body { width: 762px; height: 1200px; overflow: hidden; background: var(--paper); }
  .sheet { position: relative; width: 762px; height: 1200px; }

  .label { position: absolute; overflow: hidden; }
  .label--front { width: 420px; height: 540px; left: 0; }
  .label--back { width: 301px; height: 420px; left: 461px; }
  .label--spaetlese { top: 0; }
  .label--spaetlese-back { top: 37px; }
  .label--chardonnay { top: 660px; }
  .label--chardonnay-back { top: 697px; }

  .label .backdrop { position: absolute; inset: 0; width: 100%; height: 100%; }

  .brand {
    position: absolute; left: 22px; top: 38px; width: 376px;
    font-family: "Marcellus", serif; font-size: 66px; line-height: 1;
    letter-spacing: -1px; color: var(--gold); white-space: nowrap;
  }

  .description {
    position: absolute; width: 238px;
    font-family: Arial, "Helvetica Neue", sans-serif; font-size: 10.3px; line-height: 11px;
    color: var(--ink);
  }
  .label--spaetlese .description { left: 28px; top: 205px; }
  .label--chardonnay .description { left: 39px; top: 233px; width: 240px; }

  .grape {
    position: absolute; left: 25px; top: 318px;
    font-family: "Jost", sans-serif; font-weight: 300; font-size: 58px; line-height: 1;
    color: var(--ink);
  }

  .initial { position: absolute; background: var(--initial); }
  .label--spaetlese .initial {
    left: 56px; top: 403px; width: 72px; height: 116px;
    border-radius: 38px 10px 38px 10px;
  }
  .label--chardonnay .initial {
    left: 56px; top: 400px; width: 60px; height: 120px;
    border-radius: 60px 8px 8px 60px;
  }

  .quality {
    position: absolute; font-family: "Jost", sans-serif; font-weight: 700;
    line-height: 1; color: var(--ink); letter-spacing: 0.5px; white-space: nowrap;
  }
  .label--spaetlese .quality { left: 142px; top: 444px; font-size: 62px; }
  .label--chardonnay .quality { left: 124px; top: 444px; font-size: 36px; }

  .address {
    position: absolute; left: 22px; top: 255px;
    font-family: "Josefin Sans", sans-serif; font-weight: 300; font-size: 10.6px; line-height: 12.5px;
    color: var(--ink); font-style: normal;
  }
  .label--chardonnay-back .address { top: 257px; }

  .specs {
    position: absolute; left: 21px; right: 18px; bottom: 30px;
    display: flex; justify-content: space-between;
    font-family: "Oswald", sans-serif; font-weight: 600; font-size: 13px; color: var(--ink);
  }
  .label--chardonnay-back .specs { bottom: 28px; }
</style>
</head>
<body>
<main class="sheet">

  <!-- Gutswein: Scheurebe Spätlese, Vorderetikett -->
  <section class="label label--front label--spaetlese">
    <svg class="backdrop" viewBox="0 0 420 540" preserveAspectRatio="none" aria-hidden="true">
      <rect width="420" height="540" fill="var(--sky)"/>
      <polygon points="0,0 190,0 0,46" fill="var(--sky-light)"/>
      <polygon points="0,285 40,540 0,540" fill="var(--sky-light)"/>
      <path d="M0,476 C90,470 160,486 240,480 C320,474 380,470 420,476 L420,540 L0,540 Z" fill="var(--sky-deep)"/>
      <polygon points="240,540 420,498 420,540" fill="var(--sky-light)"/>
    </svg>
    <div class="brand">BRANDAUER</div>
    <p class="description">Lorem ipsum dolor sit amet, consectetuer adipiscing elit. Aenean commodo ligula eget dolor. Aenean massa. Cum sociis natoque penatibus et magnis dis parturient montes, nascetur ridiculus mus. Donec quam felis, ultricies nec, pellentesque eu, pretium quis, sem. Nulla consequat massa quis enim. Donec pede justo, fringilla vel, aliquet nec, vulputate eget, arcu. In enim justo, rhoncus ut, imperdiet a, venenatis vitae, justo. Nullam dictum felis eu pede mollis pretium. Integer tincidunt. Cras dapibus. Vivamus elementum semper nisi.</p>
    <h1 class="grape">Scheurebe</h1>
    <div class="initial" role="img" aria-label="Handgezeichnete Initiale S in Schwarz"></div>
    <h2 class="quality">PÄTLESE</h2>
  </section>

  <!-- Rückenetikett Spätlese -->
  <section class="label label--back label--spaetlese-back">
    <svg class="backdrop" viewBox="0 0 301 420" preserveAspectRatio="none" aria-hidden="true">
      <rect width="301" height="420" fill="var(--sky)"/>
      <polygon points="0,0 120,0 0,30" fill="var(--sky-light)"/>
      <polygon points="270,0 301,0 301,300" fill="var(--sky-light)"/>
      <polygon points="0,420 301,354 301,420" fill="var(--sky-light)"/>
    </svg>
    <address class="address">
      Familienweingut Brandauer<br>
      Jonas, Petra und Lukas Brandauer<br>
      Rebenstraße 7<br>
      67599 Beispielheim<br>
      Deutschland<br>
      Telefon: 0 61 11 - 20 48<br>
      Telefax: 0 61 11 - 20 49<br>
      e-Mail: info@weingut-brandauer-beispiel.de
    </address>
    <div class="specs"><span>11% VOL</span><span>750CL</span></div>
  </section>

  <!-- Gutswein: Chardonnay, Vorderetikett -->
  <section class="label label--front label--chardonnay">
    <svg class="backdrop" viewBox="0 0 420 540" preserveAspectRatio="none" aria-hidden="true">
      <rect width="420" height="540" fill="var(--peach)"/>
      <polygon points="0,0 190,0 0,46" fill="var(--peach-light)"/>
      <polygon points="0,285 40,540 0,540" fill="var(--peach-light)"/>
      <path d="M0,478 C90,472 170,486 250,480 C330,474 390,470 420,474 L420,540 L0,540 Z" fill="var(--river)"/>
      <path d="M0,500 C100,490 180,506 260,500 C330,494 390,490 420,492 L420,540 L0,540 Z" fill="var(--sand)"/>
      <path d="M60,515 C150,504 260,506 420,498 L420,512 C300,520 180,522 60,522 Z" fill="var(--earth)"/>
      <polygon points="240,540 420,524 420,540" fill="var(--peach-light)"/>
    </svg>
    <div class="brand">BRANDAUER</div>
    <p class="description">Lorem ipsum dolor sit amet, consectetuer adipiscing elit. Aenean commodo ligula eget dolor. Aenean massa. Cum sociis natoque penatibus et magnis dis parturient montes, nascetur ridiculus mus. Donec quam felis, ultricies nec, pellentesque eu, pretium quis, sem. Nulla consequat massa quis enim. Donec pede justo, fringilla vel, aliquet nec, vulputate eget, arcu. In enim justo, rhoncus ut, imperdiet a, venenatis vitae, justo. Nullam dictum felis eu pede mollis pretium. Integer tincidunt. Cras dapibus. Vivamus elementum semper nisi.</p>
    <div class="initial" role="img" aria-label="Handgezeichnete Initiale C in Schwarz"></div>
    <h2 class="quality">HARDONNAY</h2>
  </section>

  <!-- Rückenetikett Chardonnay -->
  <section class="label label--back label--chardonnay-back">
    <svg class="backdrop" viewBox="0 0 301 420" preserveAspectRatio="none" aria-hidden="true">
      <rect width="301" height="420" fill="var(--peach)"/>
      <polygon points="0,0 120,0 0,30" fill="var(--peach-light)"/>
      <polygon points="270,0 301,0 301,300" fill="var(--peach-light)"/>
      <polygon points="0,420 301,354 301,420" fill="var(--peach-light)"/>
    </svg>
    <address class="address">
      Familienweingut Brandauer<br>
      Jonas, Petra und Lukas Brandauer<br>
      Rebenstraße 7<br>
      67599 Beispielheim<br>
      Deutschland<br>
      Telefon: 0 61 11 - 20 48<br>
      Telefax: 0 61 11 - 20 49<br>
      e-Mail: info@weingut-brandauer-beispiel.de
    </address>
    <div class="specs"><span>11% VOL</span><span>750CL</span></div>
  </section>

</main>
</body>
</html>
```